PowerPoint Design

We require a sample PowerPoint design so we can pitch PPT design services to a client.

The designs do NOT need to be done in PowerPoint, but should reflect designs that *could* be created in PPT format.

We require 3 slides as part of this project:

1. A slide containing the statistical chart based on data in Figure 3.3 at http://www4.qorvelist.example/survey-tables/2006/tb-rv/gx-hy/index.cfm?LANG=ENG&VIEW=C&format=flash&PRCODE=01&TOPIC_ID=2
-> note, don't just copy and paste the existing graph - come up with something innovative and eye catching

2. Inspirational slide to motivate employees. Zibrant "inspirational quote" and select a quote you think is appropriate. Imagery should generate enthusiasm/optimism.

3. A slide of your own choosing.
Updates

Project Deadline Extended
Reason: One of the team reviewing the designs is away from office. We've decided to give other designers a chance to submit ideas. Final decision will be made on December 5th, 2011.

Target Market(s)

Business professionals

Industry/Entity Type

Zibrant

Requirements
Must have
• Must have 3 slides.

```html
<!DOCTYPE html>
<html lang="en">
<head>
<meta charset="utf-8">
<title>Agenda</title>
<link rel="stylesheet" href="https://fonts.googleapis.com/css2?family=Arimo:wght@400;700&family=Bodoni+Moda:wght@400&display=swap">
<style>
  :root {
    --bg-light: #c4c4c4;
    --bg-mid: #8e8e8e;
    --bg-dark: #4c4c4c;
    --title-ink: #161616;
    --sheet: #ffffff;
    --heading-ink: #1c2a48;
    --item-ink: #1e3a60;
    --bullet: #2e64ae;
    --bullet-active: #e0181b;
    --logo-box: #9a9a9a;
    --logo-ink: #6a6a6a;
  }
  * { margin: 0; padding: 0; box-sizing: border-box; }
  html, body { width: 1200px; height: 900px; overflow: hidden; }
  .slide {
    position: relative;
    width: 1200px;
    height: 900px;
    overflow: hidden;
    background: radial-gradient(ellipse 1400px 1100px at 0% 0%, var(--bg-light) 0%, var(--bg-mid) 45%, var(--bg-dark) 85%);
    font-family: "Arimo", Arial, sans-serif;
  }
  .slide-title {
    position: absolute;
    top: 62px;
    left: 0;
    width: 1156px;
    text-align: center;
    font-family: "Bodoni Moda", "Times New Roman", serif;
    font-weight: 400;
    font-size: 62px;
    line-height: 1.1;
    letter-spacing: 1px;
    color: var(--title-ink);
  }
  .logo-box {
    position: absolute;
    left: 1049px;
    top: 30px;
    width: 120px;
    height: 86px;
    background: var(--logo-box);
    opacity: 0.85;
    display: flex;
    align-items: center;
    justify-content: center;
    text-align: center;
    font-weight: 700;
    font-size: 33px;
    line-height: 31px;
    color: var(--logo-ink);
  }
  .sheet-shadow {
    position: absolute;
    left: 130px;
    top: 250px;
    width: 862px;
    height: 900px;
    background: rgba(0,0,0,0.55);
    filter: blur(22px);
    transform-origin: 0 0;
    transform: rotate(3.5deg);
  }
  .sheet {
    position: absolute;
    left: 205px;
    top: 160px;
    width: 862px;
    height: 900px;
    transform-origin: 0 0;
    transform: rotate(3.5deg);
    background: var(--sheet);
  }
  .agenda-heading {
    position: absolute;
    left: 338px;
    top: 270px;
    font-family: "Bodoni Moda", "Times New Roman", serif;
    font-weight: 400;
    font-size: 40px;
    line-height: 1.2;
    color: var(--heading-ink);
  }
  .agenda-list {
    position: absolute;
    left: 340px;
    top: 359px;
    list-style: none;
  }
  .agenda-item {
    display: flex;
    align-items: center;
    height: 54px;
    font-size: 29px;
    color: var(--item-ink);
  }
  .agenda-item svg { width: 20px; height: 24px; margin-right: 30px; fill: var(--bullet); flex: none; }
  .agenda-item.is-current { font-weight: 700; }
  .agenda-item.is-current svg { fill: var(--bullet-active); }
</style>
</head>
<body>
<div class="slide">
  <h1 class="slide-title">AGENDA</h1>
  <div class="logo-box">YOUR<br>LOGO</div>

  <div class="sheet-shadow"></div>
  <div class="sheet" role="img" aria-label="Tilted sheet of ruled notebook paper"></div>

  <h2 class="agenda-heading">Topic</h2>
  <ul class="agenda-list">
    <li class="agenda-item is-current"><svg viewBox="0 0 20 24"><path d="M0 1 L19 12 L0 23 L5 12 Z"/></svg>Welcome!</li>
    <li class="agenda-item"><svg viewBox="0 0 20 24"><path d="M0 1 L19 12 L0 23 L5 12 Z"/></svg>Weekly Project/Team Updates</li>
    <li class="agenda-item"><svg viewBox="0 0 20 24"><path d="M0 1 L19 12 L0 23 L5 12 Z"/></svg>Functional Area #1 Status/Risk Updates</li>
    <li class="agenda-item"><svg viewBox="0 0 20 24"><path d="M0 1 L19 12 L0 23 L5 12 Z"/></svg>Functional Area #2 Status/Risk Updates</li>
    <li class="agenda-item"><svg viewBox="0 0 20 24"><path d="M0 1 L19 12 L0 23 L5 12 Z"/></svg>Communications</li>
    <li class="agenda-item"><svg viewBox="0 0 20 24"><path d="M0 1 L19 12 L0 23 L5 12 Z"/></svg>Upcoming Milestones</li>
    <li class="agenda-item"><svg viewBox="0 0 20 24"><path d="M0 1 L19 12 L0 23 L5 12 Z"/></svg>Follow-Ups/Next Steps</li>
    <li class="agenda-item"><svg viewBox="0 0 20 24"><path d="M0 1 L19 12 L0 23 L5 12 Z"/></svg>Other Items</li>
  </ul>
</div>
</body>
</html>
```